Yoga Magazine needs simple business card!

We are a new yoga magazine and need a simple business card!

I also encourage you to design a text logo and maybe even incorporate some form of the "flower" pattern in the solveralogo.jpg and solverayellow.jpg files attached below. I prefer to have the "solvera" word in larger font and then "San Diego" in smaller font somewhere. See the brickhollow.jpg file or also the tarnwillet.jpg file. Our tag line will be something similar to these. If you could incorporate HEALTH, WELLNESS and YOGA LIFESTYLE into the name somehow that'd be really cool. Maybe even add in FITNESS if there is room. Also, please incorporate MAGAZINE somewhere as I want people to know what we are without having to guess.

we are SOLVERA, San Diego's original magazine for Health, Wellness and the Yoga Lifestyle.

Above all, the business card needs to be classy, clean and sophisticated. I want it to look professional.

I have included a few logos that I like. My favorite colors are the chief.jpg and the kamloops.jpg cards, but that doesn't mean that you have to use orange. I'm just looking for something that stands out.

Target Market(s)

Colors are up to you, but I'm leaning toward something soft and subtle, not bold and obnoxious. Font should be soothing and calm. Include pictures in the brochure of pretty people doing yoga, healthy looking food, families with young children. The target audience is women in their late 20s thru 50s and beyond. We will have some male readers, but maybe on 1/4 of readers will be men...so let's lean toward more feminine than masculine.

Industry/Entity Type

Business

Contact Information for Business Card

Ned Parlow
Editor-In-Chief
Solvera San Diego Magazine
847 Quillon Avenue #310
San Diego, CA 92101
www.brelvaport.com
ned@quorvix.com

Font styles to use
Serif

Requirements
Must have
• mellow, calm colors
• accent mark (') above the "e" in solvera.
Nice to have
• small logos in front of contact information that denote location, globe and phone.
• maybe just flower logo and text name on back? let's be creative here. i'll leave up to you all.
• green? yellow? orange? you pick!
• how about black and green? or green and black? :-)
Should not have
• no pictures or cartoon drawings of people doing yoga poses.
• no photography of people doing yoga poses.

```html
<!DOCTYPE html>
<html lang="en">
<head>
<meta charset="utf-8">
<title>Solvéra San Diego — Identity &amp; Business Card</title>
<link rel="stylesheet" href="https://fonts.googleapis.com/css2?family=Josefin+Sans:wght@300;400&family=Open+Sans:wght@400;600&display=swap">
<style>
  :root {
    --board-dark: #141414;
    --board-mid: #3a3b3d;
    --leaf-green: #8cc63f;
    --leaf-green-deep: #62b846;
    --sun-orange: #f7941d;
    --card-white: #ffffff;
    --card-mist: #e4e5e7;
    --ink: #111111;
    --ink-soft: #333333;
    --rule-dark: #3b3b3d;
  }
  * { margin: 0; padding: 0; box-sizing: border-box; }
  html, body { width: 1200px; height: 999px; overflow: hidden; }
  body { position: relative; background: var(--board-dark); font-family: "Open Sans", Arial, sans-serif; }

  .backdrop {
    position: absolute; inset: 0;
    background: radial-gradient(ellipse 70% 60% at 50% 55%, var(--board-mid) 0%, #232425 55%, var(--board-dark) 100%);
  }

  .brand-mark { position: absolute; left: 0; top: 0; width: 1200px; text-align: center; }
  .brand-mark__dot {
    position: absolute; left: 550px; top: 140px; width: 100px; height: 100px;
    border-radius: 50%; background: var(--sun-orange);
  }
  .brand-mark__name {
    position: absolute; left: 0; width: 1200px; top: 292px;
    font-family: "Josefin Sans", "Century Gothic", sans-serif;
    font-weight: 300; font-size: 96px; line-height: 1.1; color: var(--leaf-green); letter-spacing: 1px;
  }
  .brand-mark__place {
    position: absolute; left: 0; width: 1200px; top: 396px;
    font-family: "Josefin Sans", "Century Gothic", sans-serif;
    font-weight: 400; font-size: 38px; line-height: 1; color: var(--leaf-green); letter-spacing: 2px;
  }

  .card { position: absolute; top: 611px; width: 552px; height: 315px; border-radius: 30px; overflow: hidden; }

  .card--front { left: 18px; background: linear-gradient(180deg, var(--card-mist) 0%, var(--card-white) 38%); }
  .card__band { position: absolute; left: 0; top: 0; width: 552px; height: 315px; }

  .card-logo { position: absolute; left: 22px; top: 18px; width: 200px; text-align: center; }
  .card-logo__dot { width: 46px; height: 46px; margin: 0 auto; border-radius: 50%; background: var(--sun-orange); }
  .card-logo__name {
    font-family: "Josefin Sans", "Century Gothic", sans-serif;
    font-weight: 400; font-size: 37px; line-height: 1; margin-top: 28px; color: var(--leaf-green);
  }
  .card-logo__place {
    font-family: "Josefin Sans", "Century Gothic", sans-serif;
    font-size: 17px; line-height: 1; margin-top: 4px; letter-spacing: 1.5px; color: var(--leaf-green);
  }

  .person { position: absolute; left: 391px; top: 72px; }
  .person__name { font-size: 25px; line-height: 1; color: var(--ink); }
  .person__role { font-size: 11.5px; font-weight: 600; margin-top: 6px; color: var(--ink-soft); }

  .address { position: absolute; left: 24px; top: 234px; font-size: 14px; line-height: 19px; color: var(--card-white); font-style: normal; }
  .contacts { position: absolute; left: 372px; top: 234px; list-style: none; font-size: 14px; line-height: 19px; color: var(--card-white); }
  .contacts li { display: flex; align-items: center; gap: 6px; }
  .contacts svg { width: 12px; height: 12px; flex: none; }

  .card--back {
    left: 604px;
    background: linear-gradient(180deg, var(--leaf-green) 0%, #84c441 60%, var(--leaf-green-deep) 100%);
    color: var(--card-white); text-align: center;
  }
  .back-logo__dot { position: absolute; left: 244px; top: 44px; width: 64px; height: 64px; border-radius: 50%; background: var(--card-white); }
  .back-logo__name {
    position: absolute; left: 0; width: 552px; top: 140px;
    font-family: "Josefin Sans", "Century Gothic", sans-serif; font-weight: 400; font-size: 50px; line-height: 1.1;
  }
  .back-logo__place {
    position: absolute; left: 0; width: 552px; top: 191px;
    font-family: "Josefin Sans", "Century Gothic", sans-serif; font-size: 24px; line-height: 1; letter-spacing: 2px;
  }
  .tagline { position: absolute; left: 0; width: 552px; top: 247px; font-size: 14px; }
</style>
</head>
<body>
  <div class="backdrop" role="img" aria-label="Dark quilted diamond-pattern presentation background"></div>

  <header class="brand-mark">
    <span class="brand-mark__dot"></span>
    <h1 class="brand-mark__name">SOLVÉRA</h1>
    <p class="brand-mark__place">SAN DIEGO</p>
  </header>

  <section class="card card--front" aria-label="Business card front">
    <svg class="card__band" viewBox="0 0 552 315" aria-hidden="true">
      <defs>
        <linearGradient id="bandGreen" x1="0" y1="0" x2="0" y2="1">
          <stop offset="0" stop-color="#5fb846"/>
          <stop offset="1" stop-color="#8cc63f"/>
        </linearGradient>
      </defs>
      <path d="M0 222 Q276 180 552 222 L552 315 L0 315 Z" fill="url(#bandGreen)"/>
      <path d="M0 222 Q276 180 552 222" fill="none" stroke="var(--rule-dark)" stroke-width="4"/>
    </svg>

    <div class="card-logo">
      <div class="card-logo__dot"></div>
      <div class="card-logo__name">SOLVERA</div>
      <div class="card-logo__place">SAN DIEGO</div>
    </div>

    <div class="person">
      <div class="person__name">Ned Parlow</div>
      <div class="person__role">Editor-In-Chief</div>
    </div>

    <address class="address">
      Solvera San Diego Magazine<br>
      847 Quillon Avenue #310 San Diego,<br>
      CA 92101
    </address>

    <ul class="contacts">
      <li>
        <svg viewBox="0 0 12 12" aria-hidden="true"><rect x="1" y="1" width="10" height="10" rx="1.5" fill="none" stroke="#fff" stroke-width="1.5"/><path d="M4 3.5 L5 6 L7.5 8.5" stroke="#fff" stroke-width="1.5" fill="none"/></svg>
        000-000-0000
      </li>
      <li>
        <svg viewBox="0 0 12 12" aria-hidden="true"><rect x="3" y="1" width="6" height="4" fill="#fff"/><rect x="1" y="5" width="10" height="5" rx="1" fill="#fff"/><rect x="3" y="9" width="6" height="2" fill="#fff"/></svg>
        000-000-0000
      </li>
      <li>
        <svg viewBox="0 0 12 12" aria-hidden="true"><rect x="1" y="3" width="10" height="7" rx="1" fill="#fff"/><path d="M1.5 3.5 L6 7 L10.5 3.5" stroke="#7abf43" stroke-width="1" fill="none"/></svg>
        ned@quorvix.com
      </li>
    </ul>
  </section>

  <section class="card card--back" aria-label="Business card back">
    <span class="back-logo__dot"></span>
    <div class="back-logo__name">SOLVERA</div>
    <div class="back-logo__place">SAN DIEGO</div>
    <p class="tagline">HEALTH, WELLNESS and YOGA LIFESTYLE</p>
  </section>
</body>
</html>
```